Food broker, trader, wholesaler, liquidator looking for a 5 pages website

Looking for a 5 pages website design. We are food brokers, traders, wholesaler and closeout buyer working with manufacturers, distributors, importers sell to retailers, food service operators and industrial (ingredients). We help market their products. We are a resource for those who need a solution in the distribution/selling/placement of food on the shelves, kitchens and pantries. Whether we open new accounts with new products or sell short dated inventory, we know where to go and get results.

Target Market(s)

Food manufacturers, food distributors, food brokers

Coding

Coded - Design and coding required

Number of Pages Required

4 page

Font styles to use
Serif

Requirements
Must have
• Food-food production-warehouse-Food packaging-people meeting-trucks-supermarket shelves-

```html
<!DOCTYPE html>
<html lang="en">
<head>
<meta charset="utf-8">
<title>Harborline Trade – Home Page Variants</title>
<link href="https://fonts.googleapis.com/css2?family=Noticia+Text:wght@400;700&family=Montserrat:wght@400;500&display=swap" rel="stylesheet">
<style>
:root{
  --navy:#0d1463;
  --ink:#333844;
  --muted:#6d7080;
  --page-bg:#f3f4fa;
  --white:#ffffff;
  --footer:#262626;
  --footer-text:#e6e6e6;
  --rule:#3c3c3c;
  --card-border:#ececf0;
}
*{box-sizing:border-box;margin:0;padding:0}
html,body{width:867px;height:1200px;overflow:hidden}
body{background:var(--page-bg);font-family:"Noticia Text",Georgia,serif;color:var(--ink);position:relative;line-height:1.2}
h1,h2,h3,h4{font-weight:400}
.page{position:absolute;top:32px;width:405px;height:1130px;background:var(--white);overflow:hidden;box-shadow:0 1px 4px rgba(13,20,99,.12)}
.page--a{left:20px}
.page--b{left:443px}
.abs{position:absolute}

/* header */
.brand-mark{left:54px;top:4px;width:24px;height:24px;border-radius:50%;background:var(--navy)}
.brand-name{left:30px;top:31px;width:72px;text-align:center;font-size:4.6px;line-height:1;font-weight:700;color:var(--navy);letter-spacing:.2px;white-space:nowrap;z-index:2}
.nav{top:16px;font-size:5px;line-height:1;color:var(--ink)}
.nav--active{color:var(--navy);border-bottom:.6px solid var(--navy)}

/* hero */
.hero{left:0;top:39px;width:405px;height:204px;background:linear-gradient(180deg,#5fa6e0 0%,#a9d2f2 35%,#dcedf9 55%,#2d6fae 66%,#1b4f8d 100%)}
.hero__title{left:231px;top:76px;font-size:16.5px;line-height:1.2;color:var(--navy);white-space:nowrap}
.hero__text{left:232px;top:102px;width:150px;font-size:6.1px;line-height:12.3px;color:#3a4a66}
.hero__btn{left:232px;top:144px;width:44px;height:16px;background:var(--navy);color:var(--white);font-size:5.3px;font-weight:700;display:flex;align-items:center;justify-content:center}
.hero__dots{left:195px;top:235px;display:flex;gap:4px}
.hero__dots span{width:3.4px;height:3.4px;border-radius:50%;background:rgba(255,255,255,.55)}
.hero__dots span:first-child,.hero__dots span:last-child{background:var(--white)}

/* service icons */
.icon-row{left:38px;top:288px;width:330px;height:38px}

/* about */
.about{left:0;top:374px;width:226px;height:163px;background:var(--navy);color:var(--white)}
.about__title{left:47px;top:24px;font-size:15.5px;line-height:1.2;white-space:nowrap}
.about__rule{left:47px;top:47px;width:20px;height:1px;background:var(--white)}
.about__text{left:47px;top:57px;width:158px;font-size:4.1px;line-height:10.1px;text-align:justify;color:#e8eaf6}
.about__btn{left:47px;top:126px;width:44px;height:16px;border:.7px solid var(--white);font-size:4.6px;display:flex;align-items:center;justify-content:center}
.about__photo{left:226px;top:374px;width:179px;height:163px}
.page--a .about__photo{background:linear-gradient(180deg,#cfe3ef 0%,#9dc3d8 30%,#3f8ca8 60%,#23677f 100%)}
.page--b .about__photo{background:linear-gradient(135deg,#c9b8a4 0%,#e4d6c6 35%,#b67c5a 65%,#6b6e76 100%)}

/* section headings */
.section-title{width:405px;left:0;text-align:center;font-size:13px;line-height:16px;color:var(--navy)}
.section-sub{width:405px;left:0;text-align:center;font-size:5.3px;line-height:7px;color:var(--muted)}
.wwd-title{top:551px}
.wwd-sub{top:572px}

/* cards */
.card{top:593px;width:104px;height:131px;border:.6px solid var(--card-border);background:var(--white);box-shadow:0 0 3px rgba(0,0,0,.05)}
.card__photo{position:absolute;left:3px;top:3px;width:98px;height:72px}
.card__title{position:absolute;left:0;top:81px;width:100%;text-align:center;font-size:6.6px;line-height:1.2;color:var(--ink)}
.card__rule{position:absolute;left:45px;top:96px;width:14px;height:.8px;background:var(--navy)}
.card__text{position:absolute;left:6px;top:102px;width:92px;text-align:center;font-family:"Montserrat",Arial,sans-serif;font-size:4.1px;line-height:8.4px;color:var(--muted)}
.photo-sales{background:linear-gradient(135deg,#2e3a4d 0%,#5c6f86 50%,#b9c3cc 100%)}
.photo-trading{background:linear-gradient(135deg,#3c4a5e 0%,#7f8ca0 45%,#c9b293 100%)}
.photo-warehouse{background:linear-gradient(180deg,#c24a3c 0%,#c99a66 45%,#d7a66b 75%,#7d6f62 100%)}

/* giving back */
.giving{left:0;top:744px;width:405px;height:98px;background:var(--navy);color:var(--white);text-align:center}
.giving__title{left:0;top:24px;width:405px;font-size:13px;line-height:16px}
.giving__text{left:0;top:44px;width:405px;font-size:5.9px;line-height:11.8px}

/* contact */
.contact{left:0;top:842px;width:405px;height:162px;background:linear-gradient(180deg,#eef0f3 0%,#f6f6f4 50%,#ecebe8 100%)}
.contact-title{top:859px}
.contact-sub{top:879px}
.field{background:var(--white);border:.5px solid #d6d8de;font-size:4.1px;line-height:1;color:var(--muted);padding:4px 5px}
.submit{left:178px;top:971px;width:50px;height:16px;background:var(--navy);color:var(--white);font-size:5px;display:flex;align-items:center;justify-content:center}

/* footer */
.footer{left:0;top:1004px;width:405px;height:126px;background:var(--footer);color:var(--footer-text)}
.footer__mark{left:61px;top:1035px;width:40px;height:40px;border-radius:50%;background:var(--white)}
.footer__name{left:40px;top:1080px;width:82px;text-align:center;font-size:5.6px;line-height:1;font-weight:700;color:var(--white);white-space:nowrap}
.footer__head{top:1019px;font-size:8px;line-height:1;color:var(--white)}
.footer__list{top:1036px;list-style:none;font-family:"Montserrat",Arial,sans-serif;font-size:4.7px;line-height:11.9px;color:var(--footer-text)}
.footer__list li::before{content:"»";margin-right:6px}
.footer__follow{left:282px;top:1038px;width:85px;font-family:"Montserrat",Arial,sans-serif;font-size:4.7px;line-height:8.4px;color:var(--footer-text)}
.social{left:281px;top:1063px;display:flex;gap:2.6px}
.social span{width:12px;height:12px;border-radius:50%;border:.7px solid var(--white)}
.footer__rule{left:38px;top:1104px;width:330px;height:.5px;background:var(--rule)}
.copyright{left:0;top:1114px;width:405px;text-align:center;font-family:"Montserrat",Arial,sans-serif;font-size:4.5px;line-height:1;color:var(--footer-text)}
</style>
</head>
<body>

<!-- Variant A -->
<section class="page page--a">
  <div class="abs hero" role="img" aria-label="Container ship with tug boat at sea under a cloudy blue sky"></div>
  <header>
    <span class="abs brand-mark"></span>
    <span class="abs brand-name">HARBORLINE TRADE</span>
    <span class="abs nav nav--active" style="left:197px">Home</span>
    <span class="abs nav" style="left:226px">About Us</span>
    <span class="abs nav" style="left:263px">What we do</span>
    <span class="abs nav" style="left:306px">Contact</span>
    <span class="abs nav" style="left:339px">Giving Back</span>
  </header>

  <h1 class="abs hero__title">Harborline Trade</h1>
  <p class="abs hero__text">Sed ut perspiciatis unde omnis iste natus error sit voluptatem accusantium doloremque laudantium totam rem aperiam</p>
  <span class="abs hero__btn">Read More</span>
  <div class="abs hero__dots"><span></span><span></span><span></span></div>

  <svg class="abs icon-row" viewBox="0 0 330 38" fill="none" stroke="#0d1463" stroke-width=".9" aria-label="Service chain icons">
    <line x1="37" y1="19" x2="293" y2="19" stroke-width="1.4"/>
    <g fill="#fff"><circle cx="19" cy="19" r="18"/><circle cx="67" cy="19" r="18"/><circle cx="116" cy="19" r="18"/><circle cx="165" cy="19" r="18"/><circle cx="213" cy="19" r="18"/><circle cx="262" cy="19" r="18"/><circle cx="310" cy="19" r="18"/></g>
    <path d="M10 27V15l5 3v-3l5 3v-3l5 3V9h3v18z"/>
    <path d="M57 27V15l10-5 10 5v12zM61 27v-8h12v8"/>
    <circle cx="112" cy="13" r="2.4"/><circle cx="120" cy="13" r="2.4"/><path d="M107 27v-6a5 5 0 0 1 10 0v6M115 27v-6a5 5 0 0 1 10 0v6"/>
    <rect x="156" y="11" width="18" height="12"/><path d="M165 23v4M160 27h10M159 17h12"/>
    <path d="M203 13h13v11h-13zM216 17h5l3 4v3h-8"/><circle cx="207" cy="25" r="1.8"/><circle cx="220" cy="25" r="1.8"/>
    <path d="M253 27V12h18v15M253 17h18M253 22h18M258 12v15M265 12v15"/>
    <path d="M300 20h20a10 6 0 0 1-20 0zM306 16c0-2 2-2 2-4M311 16c0-2 2-2 2-4"/>
  </svg>

  <div class="abs about">
    <h2 class="abs about__title">About Us</h2>
    <span class="abs about__rule"></span>
    <p class="abs about__text">Harborline Trade works with food manufacturers, brand owners, distributors and wholesalers market their products. Retail, Food Service and Industrial ingredients. Founded in 2008, Harborline Trade started with the distribution of gluten free products understanding the need to provide access to unique flavors and products for the celiac consumers. From this, we expanded into deli, dairy, groceries, frozen and beverages.</p>
    <span class="abs about__btn">READ MORE</span>
  </div>
  <div class="abs about__photo" role="img" aria-label="Container ship sailing past a city port"></div>

  <h2 class="abs section-title wwd-title">What We Do</h2>
  <p class="abs section-sub wwd-sub">Sed ut perspiciatis unde omnis iste natus error sit voluptatem accusantium doloremque</p>
  <article class="abs card" style="left:38px"><div class="card__photo photo-sales" role="img" aria-label="Team meeting with sales charts on screen"></div><h3 class="card__title">Sales &amp; Marketing</h3><span class="card__rule"></span><p class="card__text">we connect food buyers and sellers through a dedicated approach.</p></article>
  <article class="abs card" style="left:150px"><div class="card__photo photo-trading" role="img" aria-label="Hands typing on a laptop with trading data"></div><h3 class="card__title">Trading</h3><span class="card__rule"></span><p class="card__text">we purchase goods anywhere and ship them Nationwide and Export.</p></article>
  <article class="abs card" style="left:263px"><div class="card__photo photo-warehouse" role="img" aria-label="Warehouse aisle with shelves and pallets"></div><h3 class="card__title">Closeout/Excess Inventory</h3><span class="card__rule"></span><p class="card__text">we buy closeouts and excess inventory for prisons, outlet stores and discounters.</p></article>

  <div class="abs giving">
    <h2 class="abs giving__title">Giving Back</h2>
    <p class="abs giving__text">We collaborate with Coastal Food Relief: South Florida's leading domestic hunger-relief<br>organization serving 25% of the state's food insecure population.</p>
  </div>

  <div class="abs contact" role="img" aria-label="Faded warehouse shelving background"></div>
  <h2 class="abs section-title contact-title">Contact Us</h2>
  <p class="abs section-sub contact-sub">Sed ut perspiciatis unde omnis iste natus error sit voluptatem accusantium</p>
  <div class="abs field" style="left:95px;top:896px;width:106px;height:14px">First Name :</div>
  <div class="abs field" style="left:204px;top:896px;width:106px;height:14px">Last Name :</div>
  <div class="abs field" style="left:95px;top:915px;width:106px;height:14px">Email :</div>
  <div class="abs field" style="left:204px;top:915px;width:106px;height:14px">Phone :</div>
  <div class="abs field" style="left:95px;top:934px;width:215px;height:29px">Message :</div>
  <span class="abs submit">SUBMIT</span>

  <footer class="abs footer"></footer>
  <span class="abs footer__mark"></span>
  <span class="abs footer__name">HARBORLINE TRADE</span>
  <h4 class="abs footer__head" style="left:133px">Quick Links</h4>
  <ul class="abs footer__list" style="left:133px"><li>Home</li><li>About Us</li><li>What we do</li><li>Contact</li><li>Giving Back</li></ul>
  <h4 class="abs footer__head" style="left:206px">Services</h4>
  <ul class="abs footer__list" style="left:206px"><li>Sed ut perspiciatis</li><li>unde omnis iste</li><li>natus error sit</li><li>voluptatem</li><li>accusantium</li></ul>
  <h4 class="abs footer__head" style="left:282px">Follow Us</h4>
  <p class="abs footer__follow">Sed ut perspiciatis unde omnis iste natus error sit voluptatem</p>
  <div class="abs social"><span></span><span></span><span></span><span></span><span></span></div>
  <span class="abs footer__rule"></span>
  <p class="abs copyright">© Copyright 2020 Harborline Trade.All Rights Reserved</p>
</section>

<!-- Variant B -->
<section class="page page--b">
  <div class="abs hero" role="img" aria-label="Container ship with tug boat at sea under a cloudy blue sky"></div>
  <header>
    <span class="abs brand-mark"></span>
    <span class="abs brand-name">HARBORLINE TRADE</span>
    <span class="abs nav nav--active" style="left:197px">Home</span>
    <span class="abs nav" style="left:226px">About Us</span>
    <span class="abs nav" style="left:263px">What we do</span>
    <span class="abs nav" style="left:306px">Contact</span>
    <span class="abs nav" style="left:339px">Giving Back</span>
  </header>

  <h1 class="abs hero__title">Harborline Trade</h1>
  <p class="abs hero__text">Sed ut perspiciatis unde omnis iste natus error sit voluptatem accusantium doloremque laudantium totam rem aperiam</p>
  <span class="abs hero__btn">Read More</span>
  <div class="abs hero__dots"><span></span><span></span><span></span></div>

  <svg class="abs icon-row" viewBox="0 0 330 38" fill="none" stroke="#0d1463" stroke-width=".9" aria-label="Service chain icons">
    <line x1="37" y1="19" x2="293" y2="19" stroke-width="1.4"/>
    <g fill="#fff"><circle cx="19" cy="19" r="18"/><circle cx="67" cy="19" r="18"/><circle cx="116" cy="19" r="18"/><circle cx="165" cy="19" r="18"/><circle cx="213" cy="19" r="18"/><circle cx="262" cy="19" r="18"/><circle cx="310" cy="19" r="18"/></g>
    <path d="M10 27V15l5 3v-3l5 3v-3l5 3V9h3v18z"/>
    <path d="M57 27V15l10-5 10 5v12zM61 27v-8h12v8"/>
    <circle cx="112" cy="13" r="2.4"/><circle cx="120" cy="13" r="2.4"/><path d="M107 27v-6a5 5 0 0 1 10 0v6M115 27v-6a5 5 0 0 1 10 0v6"/>
    <rect x="156" y="11" width="18" height="12"/><path d="M165 23v4M160 27h10M159 17h12"/>
    <path d="M203 13h13v11h-13zM216 17h5l3 4v3h-8"/><circle cx="207" cy="25" r="1.8"/><circle cx="220" cy="25" r="1.8"/>
    <path d="M253 27V12h18v15M253 17h18M253 22h18M258 12v15M265 12v15"/>
    <path d="M300 20h20a10 6 0 0 1-20 0zM306 16c0-2 2-2 2-4M311 16c0-2 2-2 2-4"/>
  </svg>

  <div class="abs about">
    <h2 class="abs about__title">About Us</h2>
    <span class="abs about__rule"></span>
    <p class="abs about__text">Harborline Trade works with food manufacturers, brand owners, distributors and wholesalers market their products. Retail, Food Service and Industrial ingredients. Founded in 2008, Harborline Trade started with the distribution of gluten free products understanding the need to provide access to unique flavors and products for the celiac consumers. From this, we expanded into deli, dairy, groceries, frozen and beverages.</p>
    <span class="abs about__btn">READ MORE</span>
  </div>
  <div class="abs about__photo" role="img" aria-label="Family shopping with a cart in a supermarket aisle"></div>

  <h2 class="abs section-title wwd-title">What We Do</h2>
  <p class="abs section-sub wwd-sub">Sed ut perspiciatis unde omnis iste natus error sit voluptatem accusantium doloremque</p>
  <article class="abs card" style="left:38px"><div class="card__photo photo-sales" role="img" aria-label="Team meeting with sales charts on screen"></div><h3 class="card__title">Sales &amp; Marketing</h3><span class="card__rule"></span><p class="card__text">we connect food buyers and sellers through a dedicated approach.</p></article>
  <article class="abs card" style="left:150px"><div class="card__photo photo-trading" role="img" aria-label="Hands typing on a laptop with trading data"></div><h3 class="card__title">Trading</h3><span class="card__rule"></span><p class="card__text">we purchase goods anywhere and ship them Nationwide and Export.</p></article>
  <article class="abs card" style="left:263px"><div class="card__photo photo-warehouse" role="img" aria-label="Warehouse aisle with shelves and pallets"></div><h3 class="card__title">Closeout/Excess Inventory</h3><span class="card__rule"></span><p class="card__text">we buy closeouts and excess inventory for prisons, outlet stores and discounters.</p></article>

  <div class="abs giving">
    <h2 class="abs giving__title">Giving Back</h2>
    <p class="abs giving__text">We collaborate with Coastal Food Relief: South Florida's leading domestic hunger-relief<br>organization serving 25% of the state's food insecure population.</p>
  </div>

  <div class="abs contact" role="img" aria-label="Faded warehouse shelving background"></div>
  <h2 class="abs section-title contact-title">Contact Us</h2>
  <p class="abs section-sub contact-sub">Sed ut perspiciatis unde omnis iste natus error sit voluptatem accusantium</p>
  <div class="abs field" style="left:95px;top:896px;width:106px;height:14px">First Name :</div>
  <div class="abs field" style="left:204px;top:896px;width:106px;height:14px">Last Name :</div>
  <div class="abs field" style="left:95px;top:915px;width:106px;height:14px">Email :</div>
  <div class="abs field" style="left:204px;top:915px;width:106px;height:14px">Phone :</div>
  <div class="abs field" style="left:95px;top:934px;width:215px;height:29px">Message :</div>
  <span class="abs submit">SUBMIT</span>

  <footer class="abs footer"></footer>
  <span class="abs footer__mark"></span>
  <span class="abs footer__name">HARBORLINE TRADE</span>
  <h4 class="abs footer__head" style="left:133px">Quick Links</h4>
  <ul class="abs footer__list" style="left:133px"><li>Home</li><li>About Us</li><li>What we do</li><li>Contact</li><li>Giving Back</li></ul>
  <h4 class="abs footer__head" style="left:206px">Services</h4>
  <ul class="abs footer__list" style="left:206px"><li>Sed ut perspiciatis</li><li>unde omnis iste</li><li>natus error sit</li><li>voluptatem</li><li>accusantium</li></ul>
  <h4 class="abs footer__head" style="left:282px">Follow Us</h4>
  <p class="abs footer__follow">Sed ut perspiciatis unde omnis iste natus error sit voluptatem</p>
  <div class="abs social"><span></span><span></span><span></span><span></span><span></span></div>
  <span class="abs footer__rule"></span>
  <p class="abs copyright">© Copyright 2020 Harborline Trade.All Rights Reserved</p>
</section>

</body>
</html>
```